Business Cards for a law firm

Business cards for our law firm. Use our silhoette logo and OAK PARTNERS - check our website (www.oakpartners.example)

Contact Information for Business Card

our silhouette logo, OAK PARTNERS, 800-555-0147, Dorian Pemberton, dorian@oakpartners.example

Requirements
Must have
• our silhouette logo, OAK PARTNERS, 800-555-0147, Dorian Pemberton, dorian@oakpartners.example

```html
<!DOCTYPE html>
<html lang="en">
<head>
<meta charset="utf-8">
<title>Oak Partners — Business Cards</title>
<link href="https://fonts.googleapis.com/css2?family=Cinzel:wght@700&family=Arimo:wght@400&display=swap" rel="stylesheet">
<style>
  :root {
    --backdrop: #dedede;
    --navy: #182f68;
    --paper: #f4f4f6;
    --stripe: #4a4a4a;
    --white: #ffffff;
    --emboss-blue: #3e6fc9;
  }
  * { margin: 0; padding: 0; box-sizing: border-box; }
  html, body { width: 1200px; height: 1040px; overflow: hidden; }
  body { background: var(--backdrop); position: relative; }

  .card {
    position: absolute;
    border-radius: 18px;
    overflow: hidden;
  }
  .card--front { left: 285px; top: 130px; width: 640px; height: 366px; background: var(--paper); }
  .card--back  { left: 284px; top: 567px; width: 646px; height: 369px; background: var(--navy); }

  .front-panel { position: absolute; inset: 0; width: 100%; height: 100%; }

  .brand-name {
    font-family: "Cinzel", serif;
    font-weight: 700;
    letter-spacing: 0.06em;
    white-space: nowrap;
  }
  .card--front .brand-name {
    position: absolute;
    left: 48px; top: 72px;
    font-size: 26px;
    color: var(--navy);
  }
  .card--back .brand-name {
    position: absolute;
    left: 0; right: 0; top: 160px;
    text-align: center;
    font-size: 38px;
    color: var(--emboss-blue);
  }

  .holder-name {
    position: absolute;
    right: 27px; top: 204px;
    font-family: "Cinzel", serif;
    font-weight: 700;
    font-size: 21px;
    letter-spacing: 0.04em;
    color: var(--white);
    white-space: nowrap;
  }

  .contact-list {
    position: absolute;
    right: 29px; top: 260px;
    list-style: none;
    font-family: "Arimo", sans-serif;
    font-size: 15.5px;
    line-height: 20px;
    color: var(--white);
  }
  .contact-list li {
    display: flex; justify-content: flex-end; align-items: center; gap: 9px;
  }
  .contact-icon { width: 13px; height: 13px; flex: none; }
</style>
</head>
<body>

  <section class="card card--front" aria-label="Business card front">
    <svg class="front-panel" viewBox="0 0 640 366" preserveAspectRatio="none" aria-hidden="true">
      <polygon points="480,0 488,0 206,366 182,366" fill="var(--stripe)"/>
      <polygon points="488,0 640,0 640,366 230,366" fill="var(--navy)"/>
    </svg>

    <div class="brand-name">OAK PARTNERS</div>

    <div class="holder-name">Dorian Pemberton</div>

    <ul class="contact-list">
      <li>800-555-0147
        <svg class="contact-icon" viewBox="0 0 24 24" aria-hidden="true"><path fill="#fff" d="M6.6 2.5l3 3.6-1.9 2.6c1.2 2.7 3.6 5.2 6.6 6.6l2.6-1.9 3.6 3-1.6 3.3c-.4.7-1.2 1-2 .8C9.3 18.6 5.4 14.7 3.5 7.1c-.2-.8.1-1.6.8-2z"/></svg>
      </li>
      <li>dorian@oakpartners.example
        <svg class="contact-icon" viewBox="0 0 24 24" aria-hidden="true"><rect x="2" y="5" width="20" height="14" fill="#fff"/><path d="M2 5l10 8 10-8" fill="none" stroke="var(--navy)" stroke-width="2"/></svg>
      </li>
      <li>www.oakpartners.example
        <svg class="contact-icon" viewBox="0 0 24 24" aria-hidden="true"><circle cx="12" cy="12" r="10" fill="#fff"/><path d="M12 2v20M2 12h20M12 2c-4 5-4 15 0 20M12 2c4 5 4 15 0 20" fill="none" stroke="var(--navy)" stroke-width="1.6"/></svg>
      </li>
    </ul>
  </section>

  <section class="card card--back" aria-label="Business card back">
    <div class="brand-name">OAK PARTNERS</div>
  </section>

</body>
</html>
```